VELMOR Website Design

We need a website designed for our company VELMOR. We are a luxury lifestyle club that will provide benefits and services for our members. The site should be clean & sleek, preferably using black and white (or darker colors). (example sites: stravenhall.example, plinth.example)

Here is a link of a sample page I did using wix. (https://dunmere7.sitehostly.example/mysite) This can be used to get a general idea.

Target Market(s)

Upper Middle Class in the United States

Number of Pages Required

5+ page

Font styles to use
Sans Serif
Other font styles liked:
• Arial (or other similar fonts)

Requirements
Must have
• A clean design that is eye-catching and speaks to our company.
Nice to have
• Ideas for copy.

```html
<!DOCTYPE html>
<html lang="en">
<head>
<meta charset="utf-8">
<title>VELMOR — A Members Only Lifestyle Club</title>
<link rel="stylesheet" href="https://fonts.googleapis.com/css2?family=Montserrat:wght@300;400;600;700&family=Open+Sans:wght@400;600&display=swap">
<style>
  :root {
    --bg: #151218;
    --bg-deep: #0f0d12;
    --purple: #a3139a;
    --purple-light: #c02cb6;
    --purple-dark: #6e0f69;
    --white: #ffffff;
    --muted: #b9b3bd;
    --label-bg: rgba(10, 8, 12, 0.72);
    --line: #2c2730;
    --icon-line: #d8d2da;
  }
  * { margin: 0; padding: 0; box-sizing: border-box; }
  html, body { width: 1200px; height: 2464px; overflow: hidden; }
  body {
    position: relative;
    background: var(--bg);
    color: var(--white);
    font-family: "Open Sans", Arial, sans-serif;
  }
  .abs { position: absolute; }

  /* Header */
  .site-header { left: 0; top: 0; width: 1200px; height: 100px; background: var(--bg-deep); }
  .brand {
    left: 84px; top: 28px;
    font-family: "Montserrat", Arial, sans-serif; font-weight: 300;
    font-size: 40px; letter-spacing: 4px; color: var(--white); white-space: nowrap;
  }
  .main-nav { right: 40px; top: 44px; display: flex; gap: 46px; }
  .main-nav a {
    font-family: "Montserrat", Arial, sans-serif; font-size: 13px; font-weight: 600;
    letter-spacing: 1px; color: var(--white); text-decoration: none; white-space: nowrap;
  }
  .main-nav a.active { color: var(--purple-light); }

  /* Hero */
  .hero {
    left: 0; top: 100px; width: 1200px; height: 640px;
    background:
      radial-gradient(ellipse at 30% 40%, rgba(196,140,96,0.55), transparent 55%),
      radial-gradient(ellipse at 75% 30%, rgba(170,110,120,0.5), transparent 55%),
      radial-gradient(ellipse at 50% 90%, rgba(60,40,70,0.8), transparent 60%),
      linear-gradient(180deg, #2a2230 0%, #3b2b2d 45%, #1a1420 100%);
  }
  .hero-title {
    left: 480px; top: 488px; width: 240px; height: 58px;
    background: var(--purple);
    font-family: "Montserrat", Arial, sans-serif; font-weight: 400;
    font-size: 40px; letter-spacing: 4px; text-align: center; line-height: 58px;
    white-space: nowrap;
  }
  .hero-tagline {
    left: 340px; top: 556px; width: 520px; height: 56px;
    background: rgba(20, 16, 24, 0.85);
    font-family: "Montserrat", Arial, sans-serif; font-weight: 400;
    font-size: 25px; letter-spacing: 1px; text-align: center; line-height: 56px;
    white-space: nowrap;
  }

  /* Benefits */
  .section-title {
    left: 0; width: 1200px; text-align: center;
    font-family: "Montserrat", Arial, sans-serif; font-weight: 600;
    font-size: 30px; letter-spacing: 1.5px;
  }
  .section-title.benefits { top: 776px; }
  .tile { width: 332px; height: 288px; overflow: hidden; }
  .tile-label {
    position: absolute; left: 0; bottom: 0; width: 100%; height: 40px;
    background: var(--label-bg);
    font-family: "Montserrat", Arial, sans-serif; font-weight: 600;
    font-size: 13px; letter-spacing: 1px; text-align: center; line-height: 40px;
    white-space: nowrap;
  }
  .tile-media { width: 100%; height: 100%; }
  .tile-feature {
    background: linear-gradient(135deg, var(--purple-light) 0%, var(--purple) 50%, var(--purple-dark) 100%);
    border: 4px solid #e7c6e5; padding: 44px 32px;
  }
  .tile-feature h3 {
    font-family: "Montserrat", Arial, sans-serif; font-weight: 600;
    font-size: 16px; letter-spacing: 1px; text-align: center; margin-bottom: 14px;
    white-space: nowrap;
  }
  .tile-feature p { font-size: 12.5px; line-height: 20px; text-align: center; color: #f2dff1; }
  .btn-pill {
    display: block; margin: 24px auto 0; width: 140px; height: 38px;
    border: 2px solid var(--white); border-radius: 20px;
    font-family: "Montserrat", Arial, sans-serif; font-size: 12px; font-weight: 600;
    letter-spacing: 1px; text-align: center; line-height: 34px; color: var(--white);
    white-space: nowrap;
  }
  .tile-feature .btn-pill { background: rgba(255,255,255,0.12); }
  .media-experiences { background: linear-gradient(180deg, #1a6f8f 0%, #0f4e6e 60%, #0a3450 100%); }
  .media-lawyer { background: linear-gradient(180deg, #6a3a26 0%, #8a5a3e 45%, #2a2226 100%); }
  .media-realestate { background: linear-gradient(160deg, #3c5a8a 0%, #7a92b8 45%, #2b3346 100%); }
  .media-events { background: linear-gradient(170deg, #4f6d35 0%, #7a5a3c 50%, #3b2a24 100%); }
  .media-jet { background: linear-gradient(180deg, #8fb6dc 0%, #d6e2ee 55%, #8a8d90 100%); }

  .view-more { left: 512px; top: 1512px; width: 176px; height: 44px; line-height: 40px; margin: 0; }

  /* About */
  .about-media {
    left: 152px; top: 1648px; width: 488px; height: 352px;
    background: radial-gradient(ellipse at 50% 25%, #d8d8d8 0%, #7a7a7a 35%, #262626 75%);
  }
  .about-panel {
    left: 504px; top: 1760px; width: 552px; height: 352px;
    background: var(--purple); padding: 44px 40px;
  }
  .about-panel h2 {
    font-family: "Montserrat", Arial, sans-serif; font-weight: 600;
    font-size: 30px; letter-spacing: 1.5px; white-space: nowrap;
  }
  .about-rule { width: 40px; height: 2px; background: var(--white); margin: 16px 0 28px; }
  .about-panel p { font-size: 13px; line-height: 21px; color: #f4e4f3; margin-bottom: 20px; }

  /* Footer */
  .footer-rule { left: 0; top: 2180px; width: 1200px; height: 1px; background: var(--line); }
  .footer-brand {
    left: 0; top: 2196px; width: 1200px; text-align: center;
    font-family: "Montserrat", Arial, sans-serif; font-weight: 300;
    font-size: 58px; letter-spacing: 6px;
  }
  .social { left: 0; top: 2312px; width: 1200px; display: flex; justify-content: center; gap: 20px; }
  .social-link {
    width: 44px; height: 44px; border: 2px solid var(--icon-line); border-radius: 50%;
    display: flex; align-items: center; justify-content: center;
  }
  .social-link i { display: block; width: 10px; height: 10px; background: var(--icon-line); }
  .copyright {
    left: 0; top: 2408px; width: 1200px; text-align: center;
    font-size: 12px; color: var(--muted);
  }
</style>
</head>
<body>
  <header class="site-header abs">
    <div class="brand abs">VELMOR</div>
    <nav class="main-nav abs">
      <a class="active" href="#">HOME</a>
      <a href="#">ABOUT</a>
      <a href="#">SERVICES &amp; BENEFITS</a>
      <a href="#">MORE...</a>
    </nav>
  </header>

  <section class="hero abs" role="img" aria-label="Photo of members celebrating and toasting with drinks at a nightclub"></section>
  <h1 class="hero-title abs">VELMOR</h1>
  <p class="hero-tagline abs">A MEMBERS ONLY LIFESTYLE CLUB</p>

  <h2 class="section-title benefits abs">BENEFITS &amp; SERVICES</h2>

  <article class="tile tile-feature abs" style="left:88px; top:872px;">
    <h3>ACCOUNTING SERVICES</h3>
    <p>Our accounting specialists help members manage tax planning, wealth reporting and private business ledgers with complete discretion.</p>
    <span class="btn-pill">READ MORE</span>
  </article>
  <article class="tile abs" style="left:438px; top:872px;">
    <div class="tile-media media-experiences" role="img" aria-label="Photo of a diver swimming in clear blue ocean water"></div>
    <div class="tile-label">EXPERIENCES</div>
  </article>
  <article class="tile abs" style="left:788px; top:872px;">
    <div class="tile-media media-lawyer" role="img" aria-label="Photo of a lawyer in a suit in front of law books"></div>
    <div class="tile-label">LAWYER SERVICES</div>
  </article>
  <article class="tile abs" style="left:88px; top:1178px;">
    <div class="tile-media media-realestate" role="img" aria-label="Photo of a real estate agent shaking hands with clients"></div>
    <div class="tile-label">REAL ESTATE SERVICES</div>
  </article>
  <article class="tile abs" style="left:438px; top:1178px;">
    <div class="tile-media media-events" role="img" aria-label="Photo of guests dining at an outdoor private event"></div>
    <div class="tile-label">PRIVATE EVENTS</div>
  </article>
  <article class="tile abs" style="left:788px; top:1178px;">
    <div class="tile-media media-jet" role="img" aria-label="Photo of a private jet parked on a runway"></div>
    <div class="tile-label">PRIVATE JET TRAVEL</div>
  </article>

  <span class="btn-pill view-more abs">VIEW MORE</span>

  <div class="about-media abs" role="img" aria-label="Black and white photo of a crowd with raised hands at a concert"></div>
  <section class="about-panel abs">
    <h2>ABOUT VELMOR</h2>
    <div class="about-rule"></div>
    <p>VELMOR is a members only lifestyle club founded to bring the finest services, experiences and opportunities to a discerning community of members, including leaders, athletes, artists and other professionals.</p>
    <p>VELMOR organizes and supports a calendar of private events and gatherings for members, where they can network with one another and build lasting relationships.</p>
  </section>

  <div class="footer-rule abs"></div>
  <div class="footer-brand abs">VELMOR</div>
  <div class="social abs" aria-label="Social links">
    <span class="social-link"><i></i></span>
    <span class="social-link"><i></i></span>
    <span class="social-link"><i></i></span>
    <span class="social-link"><i></i></span>
    <span class="social-link"><i></i></span>
    <span class="social-link"><i></i></span>
  </div>
  <p class="copyright abs">© Copyright 2015 · VELMOR All Rights Reserved.</p>
</body>
</html>
```